Maple Roster Business Card for recruitment company

We are looking for a Business Card Design that incorporates our personal details and our busines name and logo. We are a specialized search consultancy that recruit Property and Construction professionals.
We would like a business card that stands out and is appealing to the Construction and Property industry as well.

Target Market(s)

people in the construction and property industry

Contact Information for Business Card

Business Name and logo

Font styles to use
Serif

Colors
0094D4
00A9DD
6FCCEA
C7EBF8
E9F6FB

Requirements
Must have
• Business name and logo as well as contact details
Should not have
• No photos of us please

```html
<!DOCTYPE html>
<html lang="en">
<head>
<meta charset="utf-8">
<title>Maple Roster Business Card</title>
<link rel="stylesheet" href="https://fonts.googleapis.com/css2?family=Montserrat:wght@300;600&family=Open+Sans:wght@400&display=swap">
<style>
  :root {
    --page-bg: #e9ecee;
    --card-teal: #033a4e;
    --card-teal-deep: #022f40;
    --accent-blue: #0094d4;
    --accent-sky: #00a9dd;
    --ink-white: #ffffff;
    --rule-grey: #7f9aa5;
  }
  * { margin: 0; padding: 0; box-sizing: border-box; }
  html, body { width: 1200px; height: 1108px; overflow: hidden; }
  body {
    background: var(--page-bg);
    position: relative;
    font-family: "Montserrat", Arial, sans-serif;
    color: var(--ink-white);
  }
  .card {
    position: absolute;
    top: 170px;
    width: 480px;
    height: 768px;
    border-radius: 26px;
    background: var(--card-teal);
    overflow: hidden;
  }
  .card-front { left: 90px; }
  .card-back { left: 630px; }

  .brand-name {
    position: absolute;
    top: 200px;
    width: 100%;
    text-align: center;
    font-weight: 300;
    font-size: 46px;
    letter-spacing: 2px;
    text-transform: uppercase;
  }
  .holder-name {
    position: absolute;
    top: 410px;
    width: 100%;
    text-align: center;
    font-weight: 600;
    font-size: 31px;
    letter-spacing: 1px;
    text-transform: uppercase;
  }
  .holder-role {
    position: absolute;
    top: 452px;
    width: 100%;
    text-align: center;
    font-weight: 300;
    font-size: 16px;
    letter-spacing: 1.5px;
    text-transform: uppercase;
  }
  .icon-row {
    position: absolute;
    top: 494px;
    left: 60px;
    width: 360px;
    display: flex;
    align-items: center;
    gap: 8px;
  }
  .icon-row .rule { flex: 1; height: 1px; background: var(--rule-grey); }
  .icon-tile {
    width: 32px; height: 32px;
    background: var(--ink-white);
    border-radius: 6px;
    display: flex; align-items: center; justify-content: center;
  }
  .contact-list {
    position: absolute;
    top: 548px;
    width: 100%;
    text-align: center;
    font-family: "Open Sans", Arial, sans-serif;
    font-size: 20px;
    line-height: 30px;
    list-style: none;
  }
  .divider {
    position: absolute;
    top: 648px;
    left: 90px;
    width: 300px;
    height: 1px;
    background: var(--rule-grey);
  }
  .address {
    position: absolute;
    top: 668px;
    width: 100%;
    text-align: center;
    font-family: "Open Sans", Arial, sans-serif;
    font-size: 20px;
    line-height: 30px;
    font-style: normal;
  }

  .back-pattern {
    position: absolute;
    inset: 0;
    background: linear-gradient(225deg, var(--accent-sky) 0%, #0a6e93 30%, var(--card-teal) 60%, var(--card-teal-deep) 100%);
  }
  .back-brand {
    position: absolute;
    right: 44px;
    bottom: 150px;
    display: flex;
    align-items: center;
    gap: 10px;
    font-weight: 300;
    font-size: 20px;
    letter-spacing: 1px;
    text-transform: uppercase;
  }
  .back-brand .dot {
    width: 34px; height: 34px;
    border: 3px solid var(--ink-white);
    border-radius: 50%;
  }
</style>
</head>
<body>
  <section class="card card-front">
    <h1 class="brand-name">Maple Roster</h1>
    <h2 class="holder-name">Owen Carter</h2>
    <p class="holder-role">Managing Director</p>
    <div class="icon-row">
      <span class="rule"></span>
      <span class="icon-tile" aria-label="Phone">
        <svg width="20" height="20" viewBox="0 0 24 24"><path fill="#033a4e" d="M6.6 10.8a15.1 15.1 0 0 0 6.6 6.6l2.2-2.2c.3-.3.7-.4 1-.2 1.1.4 2.3.6 3.6.6.6 0 1 .4 1 1V20c0 .6-.4 1-1 1A17 17 0 0 1 3 4c0-.6.4-1 1-1h3.5c.6 0 1 .4 1 1 0 1.3.2 2.5.6 3.6.1.3 0 .7-.2 1z"/></svg>
      </span>
      <span class="icon-tile" aria-label="Email">
        <svg width="20" height="20" viewBox="0 0 24 24"><rect x="2" y="5" width="20" height="14" rx="1" fill="#033a4e"/><path d="M3 6l9 7 9-7" stroke="#fff" stroke-width="1.6" fill="none"/></svg>
      </span>
      <span class="icon-tile" aria-label="Website">
        <svg width="20" height="20" viewBox="0 0 24 24"><circle cx="12" cy="12" r="9" fill="#033a4e"/><path d="M3 12h18M12 3c3 3 3 15 0 18M12 3c-3 3-3 15 0 18" stroke="#fff" stroke-width="1.3" fill="none"/></svg>
      </span>
      <span class="rule"></span>
    </div>
    <ul class="contact-list">
      <li>021-555 0147 32</li>
      <li>hello@maplerost.com</li>
      <li>www.maplerost.com</li>
    </ul>
    <span class="divider"></span>
    <address class="address">88 Harbour Lane, Suite 4<br>30117, Northvale</address>
  </section>

  <section class="card card-back">
    <div class="back-pattern" role="img" aria-label="Repeating brand pattern fading from bright blue to deep teal"></div>
    <div class="back-brand"><span class="dot"></span>Maple Roster</div>
  </section>
</body>
</html>
```